Redesign Canvas Art E-Commerce Website

Help! I hired a couple of companies on Brisklo.com to build and design an e-commerce website for me. After three long and painful months, I have one that I believe is functional on the back-end, but aesthetically on the front end is a mess.

We are a small family business that will take your digital photo and manipulate it into a digitally created oil, watercolor or impressionist style pieces of artwork that we print on museum quality, gallery grade canvas and ship to the customer, ready to hang.

We are looking to create an e-commerce website where a customer can choose their art style, upload a photo, choose their canvas size and orientation (horizontal or vertical) and checkout. Within 48 hours, we will send them back a proof of their newly created, customized artwork for them to approve or not approve. If they approve, we print, package and ship them the product. If they do not approve, we offer unlimited revisions until they are happy.

As I mentioned, the back end functionality is already there, just need design help. No coding required

Here is a link to the development page that they created: https://plumwickstudio.com/development/

As you can see, it looks off...doesnt line up properly, wasted space, weird font. Feel free to either correct the homepage they created or design an entirely new page. I am attaching some examples of before and after photos of artwork for reference. I also think the testimonials page and shop page can use a little style. The content is there and accurate, it just doesn't look pretty. Please keep in mind that our customers will probably not be very tech savvy. The customers will probably be sending us pics of kids, grandkids, pets, family portraits, vacation photos, etc.

Here is one of our competitors - www.gildavantry.com
Their website looks clean and inviting.

Thank you in advance! Im looking forward to seeing the results. I am including our logo in the attachments (I do not have it in a vector file, just a jpeg)

Target Market(s)

Non tech-savvy indiduals, 30-70 years old

Industry/Entity Type

Please look at https://plumwickstudio.com/development/ to see various pages and what the other designers did

Number of Pages Required

1 page

Requirements
Must have
• Verbiage on pages leave "as is" but feel free to change styles. Would like to keep existing four categories on homepage
Nice to have
• Warm and inviting homepage that evokes emotion

```html
<!DOCTYPE html>
<html lang="en">
<head>
<meta charset="utf-8">
<title>Plumwick Studio – Home</title>
<link href="https://fonts.googleapis.com/css2?family=Poppins:wght@400;500;600&display=swap" rel="stylesheet">
<style>
:root{
  --orange:#f0821e;
  --orange-soft:#f7e3d2;
  --ink:#222222;
  --text:#333333;
  --muted:#555555;
  --panel:#f5f3f1;
  --white:#ffffff;
  --footer:#353535;
}
*{margin:0;padding:0;box-sizing:border-box}
html,body{width:1200px;height:3675px;overflow:hidden;background:var(--white)}
body{font-family:'Poppins',sans-serif;color:var(--text)}
.page{position:relative;width:1200px;height:3675px;overflow:hidden}
.abs{position:absolute}

/* header */
.brand{left:111px;top:28px;display:flex;align-items:center;gap:10px}
.brand-dot{width:34px;height:34px;border-radius:50%;background:var(--orange)}
.brand-name{font-size:26px;font-weight:600;color:var(--ink)}
.nav{left:458px;top:38px;display:flex;gap:23px;font-size:14.5px;color:var(--ink)}
.nav .active{font-weight:600;position:relative}
.nav .active::before{content:"";position:absolute;left:50%;top:-12px;width:8px;height:8px;margin-left:-4px;border-radius:50%;background:var(--orange)}
.cart{left:1058px;top:34px}

/* buttons */
.btn{display:flex;align-items:center;justify-content:center;width:146px;height:50px;border-radius:5px;background:var(--orange);color:var(--white);font-size:17px;font-weight:500}

/* hero */
.hero{left:111px;top:117px;width:978px;height:383px;background:var(--panel);border-radius:4px}
.hero-title{left:171px;top:178px;font-size:39px;line-height:53px;font-weight:600;color:var(--ink);width:380px}
.hero-btn{left:171px;top:378px}
.hero-visual{left:578px;top:138px;width:455px;height:338px;border-radius:6px;background:linear-gradient(135deg,#c9c3b8,#a9a48e 45%,#c98a47 80%,#e8e2da)}

/* section titles */
.section-title{left:0;width:1200px;text-align:center;font-size:38px;font-weight:600;color:var(--ink);line-height:52px}
.brush{position:absolute}

/* categories */
.cat{top:716px;width:233px;height:316px;border-radius:6px;overflow:hidden}
.cat::after{content:"";position:absolute;left:0;right:0;bottom:0;height:150px;background:linear-gradient(transparent,rgba(0,0,0,.7))}
.cat span{position:absolute;left:0;right:0;bottom:38px;text-align:center;color:var(--white);font-size:19px;font-weight:500;z-index:1}

/* about */
.about{left:0;top:1115px;width:1200px;height:551px;background:var(--panel)}
.about-photo{left:35px;top:1170px;width:495px;height:496px;background:linear-gradient(160deg,#bfae95,#7e9fb8 55%,#5c7a5a);border-radius:4px}
.about-title{left:593px;top:1176px;font-size:38px;font-weight:600;color:var(--ink)}
.about-lead{left:593px;top:1270px;width:495px;font-size:15px;line-height:28px;color:var(--ink);font-weight:500}
.about-body{left:593px;top:1339px;width:495px;font-size:15px;line-height:28.5px;color:var(--muted);text-align:justify}
.about-btn{left:593px;top:1558px}

/* tabs */
.tab{top:1891px;width:167px;height:45px;display:flex;align-items:center;justify-content:center;font-size:17px;font-weight:500;border:2px solid var(--ink)}
.tab.on{background:#2b2b2b;color:var(--white)}

/* comparisons */
.compare{width:483px;height:315px;border-radius:6px;overflow:hidden;display:flex}
.compare .half{flex:1}
.compare .divider{position:absolute;left:241px;top:0;width:2px;height:100%;background:var(--white)}
.compare .handle{position:absolute;left:224px;top:139px;width:36px;height:36px;border-radius:50%;background:var(--white)}

/* why us */
.why{width:360px;text-align:center}
.why-ring{width:150px;height:150px;border-radius:50%;border:12px solid var(--orange-soft);background:var(--white);margin:0 auto;display:flex;align-items:center;justify-content:center}
.why h3{font-size:18px;font-weight:500;color:var(--ink);margin-top:28px}
.why p{font-size:13.5px;line-height:28.5px;color:var(--muted);margin:10px auto 0;width:270px}

/* footer */
.footer{left:0;top:3392px;width:1200px;height:283px;background:var(--footer)}
.foot-brand{left:0;width:1200px;top:3448px;display:flex;justify-content:center;align-items:center;gap:10px}
.foot-nav{left:0;width:1200px;top:3533px;display:flex;justify-content:center;gap:31px;font-size:15px;color:var(--white)}
.social{left:0;width:1200px;top:3580px;display:flex;justify-content:center;gap:17px}
.social span{width:30px;height:30px;border-radius:50%;background:var(--white)}
.copy{left:0;width:1200px;top:3628px;text-align:center;font-size:14.5px;color:var(--white)}
</style>
</head>
<body>
<div class="page">

  <!-- header -->
  <div class="abs brand"><span class="brand-dot"></span><span class="brand-name">Plumwick</span></div>
  <nav class="abs nav">
    <span class="active">Home</span><span>Shop</span><span>Testimonials</span><span>About Us</span><span>FAQs</span><span>My Orders</span><span>Contact Us</span>
  </nav>
  <svg class="abs cart" width="30" height="30" viewBox="0 0 30 30">
    <path d="M3 7h4l3 12h12l3-9H9" fill="none" stroke="#222" stroke-width="1.8" stroke-linejoin="round"/>
    <circle cx="12" cy="23" r="1.8" fill="#222"/><circle cx="21" cy="23" r="1.8" fill="#222"/>
    <circle cx="25" cy="5" r="5" fill="#f0821e"/>
    <text x="25" y="7.5" font-size="7" fill="#fff" text-anchor="middle" font-family="Poppins,sans-serif">0</text>
  </svg>

  <!-- hero -->
  <div class="abs hero"></div>
  <h1 class="abs hero-title">Turn Your Digital Photos Into One of a Kind Wall Art</h1>
  <div class="abs btn hero-btn">Get Started</div>
  <div class="abs hero-visual" role="img" aria-label="A puppy photo on a tablet turned into a framed canvas painting"></div>

  <!-- categories -->
  <h2 class="abs section-title" style="top:587px">Categories</h2>
  <svg class="brush" style="left:622px;top:638px" width="132" height="14" viewBox="0 0 132 14"><path d="M2 10 Q60 0 130 5 Q70 6 8 13Z" fill="#f0821e"/></svg>

  <div class="abs cat" style="left:111px;background:linear-gradient(160deg,#3d5a2a,#a0734d 55%,#2b3a1f)" role="img" aria-label="Oil painting of a wedding couple"><span>Oil Painting</span></div>
  <div class="abs cat" style="left:360px;background:linear-gradient(160deg,#e9c9b5,#f4e2d6 50%,#d8a98e)" role="img" aria-label="Watercolor of a mother and baby"><span>Watercolor</span></div>
  <div class="abs cat" style="left:608px;background:linear-gradient(170deg,#7aa0b5,#3f7a72 45%,#b3322c 65%,#2f5d55)" role="img" aria-label="Impressionist painting of a canal scene"><span>Impressionist</span></div>
  <div class="abs cat" style="left:856px;background:linear-gradient(160deg,#9fa48f,#d7b59c 50%,#5e7f86)" role="img" aria-label="Photo of two children eating ice cream"><span>Digital Photo</span></div>

  <!-- about -->
  <div class="abs about"></div>
  <div class="abs about-photo" role="img" aria-label="Grandparents hugging beside a framed canvas of themselves"></div>
  <h2 class="abs about-title">About Us</h2>
  <svg class="brush" style="left:600px;top:1222px" width="190" height="14" viewBox="0 0 190 14"><path d="M2 10 Q90 0 188 5 Q100 6 8 13Z" fill="#f0821e"/></svg>
  <p class="abs about-lead">At Plumwick Studio, we take your digital photo and turn it into a one-of-a-kind piece of artwork!</p>
  <p class="abs about-body">The process couldn't be any easier. Simply upload your photo, choose your art style and size, and let our team of skilled digital artists do the rest. Do you want to put your digital photo on canvas without an art style? No problem! Just choose the "Digital Photo/Retouching" category and upload your photo. We can print your photo "as is" or do some minor retouching (e.g. remove objects, enhance colors, lighten photo, etc)</p>
  <div class="abs btn about-btn">Learn More</div>

  <!-- before / after -->
  <h2 class="abs section-title" style="top:1736px">From Photo to Museum<br>Quality Canvas Art</h2>
  <svg class="brush" style="left:666px;top:1842px" width="130" height="14" viewBox="0 0 130 14"><path d="M2 10 Q60 0 128 5 Q70 6 8 13Z" fill="#f0821e"/></svg>

  <div class="abs tab on" style="left:442px">Horizontal</div>
  <div class="abs tab" style="left:622px">Vertical</div>

  <div class="abs compare" style="left:111px;top:2019px" role="img" aria-label="Before and after of a child walking with a parent on a forest path">
    <div class="half" style="background:linear-gradient(160deg,#3f4a2c,#8b8170)"></div>
    <div class="half" style="background:linear-gradient(160deg,#d8c79a,#7a8a99 50%,#6e6758)"></div>
    <div class="divider"></div><div class="handle"></div>
  </div>
  <div class="abs compare" style="left:607px;top:2019px" role="img" aria-label="Before and after of a dog and a cat resting">
    <div class="half" style="background:linear-gradient(160deg,#e9e6e2,#7a4a26 60%,#efece8)"></div>
    <div class="half" style="background:linear-gradient(160deg,#c9622a,#e4954b 50%,#d9c9b8)"></div>
    <div class="divider"></div><div class="handle"></div>
  </div>
  <div class="abs compare" style="left:111px;top:2353px" role="img" aria-label="Before and after of a mother kissing her baby">
    <div class="half" style="background:linear-gradient(160deg,#f4f2f0,#e6c6b1 60%,#f1ede9)"></div>
    <div class="half" style="background:linear-gradient(160deg,#e9c4ad,#f5e6dc 55%,#fbf6f2)"></div>
    <div class="divider"></div><div class="handle"></div>
  </div>
  <div class="abs compare" style="left:607px;top:2353px" role="img" aria-label="Before and after of a wedding couple among ivy">
    <div class="half" style="background:linear-gradient(160deg,#2c3d1f,#5a6b3a 50%,#d9d2c7)"></div>
    <div class="half" style="background:linear-gradient(160deg,#3d5a2a,#9c6a45 50%,#2e3d22)"></div>
    <div class="divider"></div><div class="handle"></div>
  </div>

  <div class="abs btn" style="left:527px;top:2714px">Get Started</div>

  <!-- why us -->
  <h2 class="abs section-title" style="top:2866px">Why us?</h2>
  <svg class="brush" style="left:605px;top:2917px" width="130" height="14" viewBox="0 0 130 14"><path d="M2 10 Q60 0 128 5 Q70 6 8 13Z" fill="#f0821e"/></svg>

  <div class="abs why" style="left:60px;top:2969px">
    <div class="why-ring">
      <svg width="60" height="60" viewBox="0 0 60 60" fill="none" stroke="#9a5a2a" stroke-width="2">
        <path d="M30 18a10 10 0 0 0-6 18v5h12v-5a10 10 0 0 0-6-18z"/><path d="M25 45h10"/>
        <path d="M30 6v5M14 14l4 4M46 14l-4 4M8 30h5M47 30h5" stroke="#f0821e"/>
      </svg>
    </div>
    <h3>Your Idea Your Design</h3>
    <p>Each art piece is customized for you! You choose your size, orientation and art style. Makes a perfect gift!!!</p>
  </div>
  <div class="abs why" style="left:420px;top:2969px">
    <div class="why-ring">
      <svg width="70" height="60" viewBox="0 0 70 60" fill="none" stroke="#9a5a2a" stroke-width="2">
        <path d="M24 20l18-8 18 8v22l-18 8-18-8z"/><path d="M24 20l18 8 18-8M42 28v22"/>
        <path d="M6 26h12M10 32h8M4 38h14" stroke="#f0821e"/>
      </svg>
    </div>
    <h3>Fast Shipping</h3>
    <p>Your artwork is printed and shipped in the USA! We offer fast turnaround with transit times typically 3-7 days. Free tracking with each order!!</p>
  </div>
  <div class="abs why" style="left:780px;top:2969px">
    <div class="why-ring">
      <svg width="60" height="60" viewBox="0 0 60 60" fill="none" stroke="#9a5a2a" stroke-width="2">
        <circle cx="30" cy="24" r="14"/><path d="M24 24l4 4 8-8" stroke="#f0821e"/>
        <path d="M22 36l-6 14 7-2 4 6 3-16M38 36l6 14-7-2-4 6-3-16"/>
      </svg>
    </div>
    <h3>High Quality</h3>
    <p>We've put a lot of effort ensuring your artwork is of the highest quality. Each piece is printed on the highest quality, gallery grade canvas. It is ready to hang upon arrival.!</p>
  </div>

  <!-- footer -->
  <footer class="abs footer"></footer>
  <div class="abs foot-brand"><span class="brand-dot" style="width:28px;height:28px"></span><span class="brand-name" style="color:#fff;font-size:24px">Plumwick</span></div>
  <nav class="abs foot-nav"><span>Home</span><span>Shop</span><span>Testimonials</span><span>About Us</span><span>FAQs</span><span>My Orders</span><span>Contact Us</span></nav>
  <div class="abs social"><span></span><span></span><span></span><span></span></div>
  <p class="abs copy">2023 Plumwick Studio. All Rights Reserved.</p>

</div>
</body>
</html>
```